Northvale Strategy Partners Website Design

I need a website design for my new business consulting and executive coaching firm, Northvale Strategy Partners. We provide consultative services to business C-suites as well as personal coaching to executives. I have attached the logo with color scheme I have chosen. I would like the website to reflect professionalism and continue the color scheme in the logo.

Target Market(s)

Small to medium business and their executives; middle to upper income men and women in mid- to late career looking for significance

Industry/Entity Type

Business Consultant

Number of Pages Required

4 page

Requirements
Must have
• A homepage with prominent logo and way to contact for more information; an area on the homepage with easy to read, clear text to describe what the company does; a prominent area on the homepage for a tagline; a blog page that can be updated regularly, an "about us" page with biographical information; an "about us" page; a page detailing services offered
• The web design must match the logo colors and font that I have uploaded.
Nice to have
• A lighthouse picture in the background or header
Should not have
• A lot of text area on the homepage

```html
<!DOCTYPE html>
<html lang="en">
<head>
<meta charset="utf-8">
<title>Northvale Strategy Partners</title>
<link href="https://fonts.googleapis.com/css2?family=Raleway:wght@400;500;600;700&family=Roboto:wght@400&display=swap" rel="stylesheet">
<style>
:root{
  --maroon:#7a1020;
  --blue:#1a73c9;
  --link:#3aa3e0;
  --navy:#1b2f5e;
  --band:#162a56;
  --ink:#1a1a1a;
  --muted:#555;
  --card:#f2f2f2;
  --dark:#2a2a2a;
}
*{margin:0;padding:0;box-sizing:border-box}
html,body{width:1200px;height:1200px;overflow:hidden}
body{position:relative;font-family:'Raleway',sans-serif;color:var(--ink);background:#fff}
.abs{position:absolute}
.news-section{left:0;top:0;width:1200px;height:506px;background:linear-gradient(135deg,#e9ebee 0%,#f6f7f8 45%,#e4e6e9 100%)}
.col-title{font-size:26px;font-weight:400;color:var(--maroon);top:50px}
.col-title::after{content:"";position:absolute;left:0;top:38px;width:26px;height:2px;background:var(--maroon)}
.card{top:96px;width:249px;height:314px;background:var(--card);border:1px solid #ddd;box-shadow:0 6px 8px -4px rgba(0,0,0,.35)}
.card-photo{width:100%;height:78px}
.press-photo{background:linear-gradient(120deg,#2d5f86,#8fb4cc 55%,#1f3f5c)}
.blog-photo{background:linear-gradient(120deg,#c9cdd3,#5b6270 50%,#e3e6ea)}
.press-item{margin:14px 12px 0 12px}
.date{font-size:9.5px;color:var(--blue)}
.press-item p{font-size:11.2px;line-height:15px;margin-top:3px}
.blog-item{margin:13px 12px 0 12px}
.blog-item p{font-size:11px;line-height:12.6px}
.blog-item .meta{font-size:9.5px;color:var(--blue);font-weight:600;margin-top:3px}
.tweet{left:486px;width:230px}
.tweet .icon{position:absolute;left:0;top:1px}
.tweet p{margin-left:26px;font-size:9.2px;line-height:14px;color:var(--muted)}
.tweet p a{color:var(--link);font-size:11px;text-decoration:none}
.tweet .time{margin-left:0;margin-top:8px;display:flex;align-items:center;font-size:9px;color:var(--blue)}
.tweet .time::before{content:"";width:20px;border-top:1px dotted #aaa;margin-right:4px}
.tweet .time::after{content:"";flex:1;border-top:1px solid #ddd;margin-left:6px}
.btn{top:424px;width:98px;height:35px;border:2px solid var(--navy);background:#fff;color:var(--navy);font-weight:700;font-size:11px;letter-spacing:.3px;display:flex;align-items:center;justify-content:center}
.testimonial{left:0;top:506px;width:1200px;height:294px;background:linear-gradient(90deg,#3a3b3d 0%,#4a4a4b 50%,#333436 100%)}
.testimonial h2{position:absolute;top:58px;width:100%;text-align:center;color:#fff;font-size:17px;font-weight:700}
.testimonial h2::after{content:"";position:absolute;left:518px;top:26px;width:26px;height:2px;background:#fff}
.quote{position:absolute;left:338px;top:136px;width:534px;color:#fff;font-size:12.6px;line-height:22.5px;text-align:center}
.quote .mark{color:var(--link);font-size:14px}
.quote-name{position:absolute;top:204px;width:100%;text-align:center;color:#fff;font-weight:700;font-size:12.5px}
.touch-band{left:0;top:800px;width:1200px;height:103px;background:var(--band);display:flex;align-items:center;justify-content:center;gap:25px}
.touch-band h3{color:#fff;font-weight:700;font-size:21px;margin-right:2px}
.social{width:46px;height:46px;border-radius:9px;background:#1570c4;color:#fff;font-size:8.5px;font-weight:600;display:flex;align-items:center;justify-content:center;margin-left:-15px}
.social:first-of-type{margin-left:0}
.contact{left:0;top:903px;width:1200px;height:297px;background:linear-gradient(180deg,#2a2a2b,#232324)}
.contact h2{position:absolute;top:34px;width:100%;text-align:center;color:#fff;font-size:21px;font-weight:700}
.field{position:absolute;background:#fff;font-family:'Roboto',sans-serif;font-size:10.5px;color:#333;padding:13px 14px}
.submit{position:absolute;top:287px;width:127px;height:20px;border:1px solid #ccc;border-bottom:none}
</style>
</head>
<body>

<section class="abs news-section" role="img" aria-label="Soft blurred background of business charts and documents"></section>

<h2 class="abs col-title" style="left:213px">Press Releases</h2>
<h2 class="abs col-title" style="left:472px">Latest Tweets</h2>
<h2 class="abs col-title" style="left:737px">Executive Blog</h2>

<article class="abs card" style="left:213px">
  <div class="card-photo press-photo" role="img" aria-label="Photo of a hand touching a glowing screen"></div>
  <div class="press-item"><div class="date">January 10, 2015</div><p>Announce Fourth Quarter and Fiscal Year 2014 Financial Results on February 11, 2015.</p></div>
  <div class="press-item"><div class="date">January 3, 2015</div><p>Global Study Finds 100 Percent of Retail, 91 Percent of Entertainment and Media Organizations Breached in Trial</p></div>
  <div class="press-item"><div class="date">December 20, 2014</div><p>Threat Analytics Platform Integrated with LogSentry to Increase Security Visibility Across the Enterprise</p></div>
</article>

<div class="abs tweet" style="top:103px">
  <svg class="icon" width="16" height="14" viewBox="0 0 16 14"><path d="M8 1.5C4.4 1.5 1.5 3.6 1.5 6.3c0 1.5.9 2.8 2.3 3.7L3 12.8l3.3-1.8c.5.1 1.1.2 1.7.2 3.6 0 6.5-2.1 6.5-4.9S11.6 1.5 8 1.5z" fill="none" stroke="#1a73c9" stroke-width="1.8"/></svg>
  <p>Most inspiring meeting ever! RT <a>@MarcusHollen</a> Amazing meeting with the fantastic people</p>
  <div class="time">12h ago</div>
</div>
<div class="abs tweet" style="top:186px">
  <svg class="icon" width="16" height="14" viewBox="0 0 16 14"><path d="M8 1.5C4.4 1.5 1.5 3.6 1.5 6.3c0 1.5.9 2.8 2.3 3.7L3 12.8l3.3-1.8c.5.1 1.1.2 1.7.2 3.6 0 6.5-2.1 6.5-4.9S11.6 1.5 8 1.5z" fill="none" stroke="#1a73c9" stroke-width="1.8"/></svg>
  <p><a>@Tweetwise</a> Mobile Pro now comes with a lockscreen widget for Mobile 4.2</p>
  <div class="time">6 days ago</div>
</div>
<div class="abs tweet" style="top:255px">
  <svg class="icon" width="16" height="14" viewBox="0 0 16 14"><path d="M8 1.5C4.4 1.5 1.5 3.6 1.5 6.3c0 1.5.9 2.8 2.3 3.7L3 12.8l3.3-1.8c.5.1 1.1.2 1.7.2 3.6 0 6.5-2.1 6.5-4.9S11.6 1.5 8 1.5z" fill="none" stroke="#1a73c9" stroke-width="1.8"/></svg>
  <p>15+ Comprehensive Responsive Web Design Tutorials <a>http://lnk.to/WbDsg</a> /via <a>@larkstudio</a></p>
  <div class="time">12h Ago</div>
</div>
<div class="abs tweet" style="top:339px">
  <svg class="icon" width="16" height="14" viewBox="0 0 16 14"><path d="M8 1.5C4.4 1.5 1.5 3.6 1.5 6.3c0 1.5.9 2.8 2.3 3.7L3 12.8l3.3-1.8c.5.1 1.1.2 1.7.2 3.6 0 6.5-2.1 6.5-4.9S11.6 1.5 8 1.5z" fill="none" stroke="#1a73c9" stroke-width="1.8"/></svg>
  <p>Most inspiring meeting ever! RT <a>@Dana Whitfield</a> Amazing meeting with the fantastic people</p>
  <div class="time">12h ago</div>
</div>

<article class="abs card" style="left:737px">
  <div class="card-photo blog-photo" role="img" aria-label="Photo of a smiling business team in an office"></div>
  <div class="blog-item"><p>Announce Fourth Quarter and Fiscal Year 2014 Financial Results on February 11, 2015.</p><div class="meta">Post: Dana Whitfield, January 10, 2015</div></div>
  <div class="blog-item"><p>Global Study Finds 100 Percent of Retail, 91 Percent of Entertainment and Media Organizations Breached in Trial</p><div class="meta">Post: Dana Whitfield, January 10, 2015</div></div>
  <div class="blog-item"><p>Things are going better than I could've imagined. I started almost 4.5 months ago and have made 7% return. These market changes have provided a lot of learning lessons. Looking forward to trying some new strategies.</p><div class="meta">Post: Dana Whitfield, January 10, 2015</div></div>
</article>

<div class="abs btn" style="left:289px">VIEW MORE</div>
<div class="abs btn" style="left:548px">FOLLOW US</div>
<div class="abs btn" style="left:813px">VIEW MORE</div>

<section class="abs testimonial" role="img" aria-label="Dimmed photo of a man working at a laptop">
  <h2>What Our Client Say</h2>
  <p class="quote"><span class="mark">“</span> Lorem ipsum dolor sit amet, consectetur adipisicing elit, sed do eiusmod tempor incididunt ut labore et dolore magna aliqua. Ut enim ad minim veniam, quis nostrud exercitation ullamco <span class="mark">”</span></p>
  <div class="quote-name">Dana Whitfield</div>
</section>

<section class="abs touch-band">
  <h3>YOU SHOULD STAY IN TOUCH!</h3>
  <div class="social">Chirpline</div>
  <div class="social">Reelcast</div>
  <div class="social">Linkfold</div>
</section>

<section class="abs contact" role="img" aria-label="Dark street map background">
  <h2>CONTACT US</h2>
  <div class="field" style="left:247px;top:85px;width:344px;height:34px">NAME</div>
  <div class="field" style="left:607px;top:85px;width:345px;height:34px">EMAIL</div>
  <div class="field" style="left:247px;top:152px;width:705px;height:103px">MESSAGE</div>
  <div class="submit" style="left:465px"></div>
  <div class="submit" style="left:607px"></div>
</section>

</body>
</html>
```